Evaporative Air Conditioning Summer Service

Would like to design a flyer to send out in an email to existing clients to promote a Pre-summer service for Evaporative Air Conditioners
Cost will be $110.00 inc gst
Tasks included in service are
- Inspection and clean of pads
- Inspection and check float valve, water pump, fan, motor, bearings, drain
- Clean basin
- Supply of bacterial tablet
- Inspect overall condition of unit
- Any repairs if required will be quoted
Please see files attached of a previous very basic flyer I have used for installation and replacement unit costs. This has current contact information
Have also uploaded company logo for use.
Thanks
Plumbing

```html
<!DOCTYPE html>
<html lang="en">
<head>
<meta charset="utf-8">
<title>Pre-Summer Service for Evaporative Air Conditioners</title>
<link rel="stylesheet" href="https://fonts.googleapis.com/css2?family=Montserrat:ital,wght@0,500;0,600;0,700;0,800;1,600&family=Oswald:wght@600;700&display=swap">
<style>
  :root {
    --blue: #1e5fb5;
    --blue-dark: #17479a;
    --orange: #f39a1e;
    --orange-deep: #f07b22;
    --ink: #2b2b2b;
    --sky: #a8dbf1;
    --sky-pale: #e9f6fc;
    --peach: #fde0ad;
    --line: #f3dcc0;
  }
  * { margin: 0; padding: 0; box-sizing: border-box; }
  html, body { width: 671px; height: 1200px; overflow: hidden; }
  body {
    position: relative;
    font-family: "Montserrat", sans-serif;
    color: var(--ink);
    background: linear-gradient(180deg, var(--sky) 0%, var(--sky-pale) 22%, #f6fbfd 45%, #fdf3e0 75%, var(--peach) 100%);
  }
  .abs { position: absolute; }
  .brand {
    top: 92px; left: 0; width: 100%;
    display: flex; justify-content: center; align-items: center; gap: 10px;
  }
  .brand-dot { width: 22px; height: 22px; border-radius: 50%; background: var(--orange); }
  .brand-name { font-weight: 800; font-size: 26px; color: var(--blue); letter-spacing: 0.5px; }
  .headline {
    top: 192px; left: 0; width: 100%; text-align: center;
    font-family: "Oswald", sans-serif; font-weight: 700; font-size: 50px;
    color: var(--blue); letter-spacing: 1.5px; line-height: 1;
  }
  .subhead {
    top: 257px; left: 62px; width: 547px;
    display: flex; align-items: center; gap: 12px;
    font-family: "Oswald", sans-serif; font-weight: 700; font-size: 31px;
    color: var(--orange); letter-spacing: 1.4px; line-height: 1; white-space: nowrap;
  }
  .subhead::before, .subhead::after { content: ""; flex: 1; height: 2px; background: var(--orange); }
  .tasks-pill {
    top: 333px; left: 134px; width: 404px; height: 39px;
    background: var(--blue); border-radius: 20px;
    color: #fff; font-weight: 600; font-size: 15px; letter-spacing: 0.6px;
    display: flex; align-items: center; justify-content: center;
  }
  .task-list { list-style: none; font-size: 14px; font-weight: 500; line-height: 1.35; letter-spacing: 0.3px; }
  .task-list li { position: relative; padding-left: 18px; margin-bottom: 10px; }
  .task-list li::before {
    content: ""; position: absolute; left: 0; top: 4px; width: 10px; height: 10px;
    border-radius: 50%; background: var(--orange);
  }
  .task-list.left { top: 395px; left: 64px; width: 290px; }
  .task-list.right { top: 395px; left: 373px; width: 250px; }
  .units-image {
    top: 540px; left: 97px; width: 488px; height: 318px;
    border-radius: 8px;
    background: linear-gradient(160deg, #ffffff 0%, #e6eaee 55%, #c9cfd5 100%);
  }
  .price-band { top: 824px; left: 64px; width: 545px; height: 112px; }
  .price-band svg { display: block; }
  .cost-label {
    top: 846px; left: 108px; width: 210px; text-align: center;
    font-style: italic; font-weight: 600; font-size: 19px; color: #fff; letter-spacing: 0.5px;
  }
  .price {
    top: 865px; left: 314px; color: #fff; white-space: nowrap;
    font-family: "Oswald", sans-serif; font-weight: 700; font-size: 48px; line-height: 1; font-style: italic;
  }
  .price small { font-family: "Montserrat", sans-serif; font-weight: 600; font-size: 20px; letter-spacing: 0.5px; margin-left: 6px; }
  .contact-pill {
    top: 983px; left: 240px; width: 192px; height: 45px; border-radius: 23px;
    background: linear-gradient(180deg, var(--orange) 0%, var(--orange-deep) 100%);
    color: #fff; font-family: "Oswald", sans-serif; font-weight: 600; font-size: 20px; letter-spacing: 1.5px;
    display: flex; align-items: center; justify-content: center;
  }
  .phone {
    top: 1048px; left: 0; width: 100%; text-align: center;
    font-weight: 800; font-size: 27px; letter-spacing: 2px; color: #222;
  }
  .rule { left: 97px; width: 476px; height: 1px; background: var(--line); }
  .email {
    top: 1101px; left: 0; width: 100%; text-align: center;
    font-weight: 500; font-size: 15px; letter-spacing: 1.4px;
  }
  .abn {
    top: 1141px; left: 0; width: 100%; text-align: center;
    font-weight: 600; font-size: 15px; letter-spacing: 0.8px;
  }
  .abn b { font-weight: 800; margin-right: 6px; }
</style>
</head>
<body>
  <header class="abs brand">
    <span class="brand-dot"></span>
    <span class="brand-name">Summit Gas &amp; Plumbing</span>
  </header>

  <h1 class="abs headline">PRE-SUMMER SERVICE FOR</h1>
  <h2 class="abs subhead">EVAPORATIVE AIR CONDITIONERS</h2>

  <div class="abs tasks-pill">TASKS INCLUDED IN SERVICE ARE</div>

  <ul class="abs task-list left">
    <li>Inspection &amp; clean of pads</li>
    <li>Inspection &amp; check float valve, water pump, fan, motor, bearings, drain</li>
    <li>Clean basin</li>
  </ul>
  <ul class="abs task-list right">
    <li>Supply of bacterial tablet</li>
    <li>Inspect overall condition of unit</li>
    <li>Any repairs if required will be quoted</li>
  </ul>

  <div class="abs units-image" role="img" aria-label="Group of white air conditioning units: portable evaporative cooler, split system, outdoor fan unit, tower fan and remote controls"></div>

  <div class="abs price-band">
    <svg width="545" height="112" viewBox="0 0 545 112">
      <defs>
        <linearGradient id="bandBlue" x1="0" y1="0" x2="1" y2="0">
          <stop offset="0" stop-color="#1c54a8"/>
          <stop offset="1" stop-color="#2368c2"/>
        </linearGradient>
        <linearGradient id="tabOrange" x1="0" y1="0" x2="0" y2="1">
          <stop offset="0" stop-color="#f6a623"/>
          <stop offset="1" stop-color="#f07b22"/>
        </linearGradient>
      </defs>
      <path d="M20 56 L545 28 Q530 80 510 104 L0 108 Q8 80 20 56 Z" fill="url(#bandBlue)"/>
      <path d="M46 12 Q56 2 70 2 L262 2 L236 58 Q230 66 218 66 L28 66 Q36 30 46 12 Z" fill="url(#tabOrange)"/>
    </svg>
  </div>
  <div class="abs cost-label">COST WILL BE</div>
  <div class="abs price">$110.00<small>INC GST</small></div>

  <div class="abs contact-pill">CONTACT US</div>
  <div class="abs phone">0400123987</div>
  <div class="abs rule" style="top:1092px"></div>
  <div class="abs email">admin@summitgasandplumbing.com.au</div>
  <div class="abs rule" style="top:1129px"></div>
  <div class="abs abn"><b>ABN</b>51824753556</div>
</body>
</html>
```